Stylish Business Cards Wanted

- DOUBLE SIDED Design Required -

High end, edgy cards for a corporate and personal stylist. Must include logo,
Name: Belinda Harwick
Title: Director and Stylist
telephone : +61 8 7142 5809
email: belinda@theloombriefing.example
website: theloombriefing.example
Tag: Corporate Workwear & Uniform Specialist | Personal Stylist
Would like nice icons for telephone, email, website

Target Market(s)

Businesses wanting stylish uniforms, people wanting stylish wardrobes

Industry/Entity Type

Corporate Workwear Stylist

Contact Information for Business Card

I would like black, white and gold foiling incorporated in the design - possibly a touch of the other colours on my branding guide attached Name: Belinda Harwick Title: Director and Stylist telephone : +61 8 7142 5809 email: belinda@theloombriefing.example website: theloombriefing.example Tag: Corporate Workwear & Uniform Specialist | Personal Stylist Would like nice icons for telephone, email, website

Font styles to use
Other font styles liked:
• Raleway

Colors

Designer to choose colors to be used in the design.

Requirements
Must have
• Gold foil accents

```html
<!DOCTYPE html>
<html lang="en">
<head>
<meta charset="utf-8">
<title>The Loom Briefing — Business Card</title>
<link rel="stylesheet" href="https://fonts.googleapis.com/css2?family=Raleway:wght@300;400;600;700&display=swap">
<style>
  :root {
    --backdrop: #dcd9d5;
    --card: #f3f2f0;
    --card-edge: #ffffff;
    --ink: #1d1d1d;
    --ink-soft: #3a3a3a;
    --gold: #c9a24a;
  }
  * { margin: 0; padding: 0; box-sizing: border-box; }
  html, body {
    width: 1200px;
    height: 1038px;
    overflow: hidden;
    background: var(--backdrop);
    font-family: "Raleway", sans-serif;
    color: var(--ink);
  }
  .business-card {
    position: absolute;
    left: 80px;
    top: 218px;
    width: 1040px;
    height: 602px;
    background: var(--card);
    border: 2px solid var(--card-edge);
    border-radius: 24px;
    box-shadow: 0 10px 30px rgba(0,0,0,0.12);
  }
  .brand {
    position: absolute;
    left: 96px;
    top: 232px;
    width: 320px;
    display: flex;
    align-items: center;
    gap: 14px;
  }
  .brand-square {
    width: 18px;
    height: 18px;
    background: var(--ink);
    flex: none;
  }
  .brand-name {
    font-size: 38px;
    font-weight: 600;
    line-height: 1.05;
    letter-spacing: 0.5px;
    color: var(--ink);
  }
  .divider {
    position: absolute;
    left: 453px;
    top: 186px;
    width: 3px;
    height: 248px;
    background: var(--ink);
  }
  .identity {
    position: absolute;
    left: 505px;
    top: 196px;
  }
  .person-name {
    font-size: 44px;
    font-weight: 600;
    color: var(--ink);
    line-height: 1.1;
  }
  .person-title {
    margin-top: 2px;
    margin-left: 6px;
    font-size: 21px;
    font-weight: 700;
    color: var(--gold);
  }
  .contact-list {
    position: absolute;
    left: 512px;
    top: 296px;
    list-style: none;
  }
  .contact-item {
    display: flex;
    align-items: center;
    height: 45px;
    font-size: 24px;
    font-weight: 400;
    color: var(--ink-soft);
  }
  .contact-icon {
    width: 22px;
    height: 22px;
    margin-right: 16px;
    fill: var(--ink);
    flex: none;
  }
  .tagline {
    position: absolute;
    left: 92px;
    top: 538px;
    font-size: 28px;
    font-weight: 300;
    color: var(--ink-soft);
  }
</style>
</head>
<body>
  <main class="business-card">
    <div class="brand">
      <span class="brand-square"></span>
      <span class="brand-name">The Loom<br>Briefing</span>
    </div>

    <div class="divider"></div>

    <div class="identity">
      <h1 class="person-name">Belinda Harwick</h1>
      <p class="person-title">Director and Stylist</p>
    </div>

    <ul class="contact-list">
      <li class="contact-item">
        <svg class="contact-icon" viewBox="0 0 24 24" aria-hidden="true">
          <path d="M6.6 10.8a15.1 15.1 0 0 0 6.6 6.6l2.2-2.2a1 1 0 0 1 1-.25 11.4 11.4 0 0 0 3.6.57 1 1 0 0 1 1 1V20a1 1 0 0 1-1 1A17 17 0 0 1 3 4a1 1 0 0 1 1-1h3.5a1 1 0 0 1 1 1c0 1.25.2 2.45.57 3.57a1 1 0 0 1-.25 1z"/>
        </svg>
        +61 8 7142 5809
      </li>
      <li class="contact-item">
        <svg class="contact-icon" viewBox="0 0 24 24" aria-hidden="true">
          <path d="M2 5h20v14H2z M3.5 6.5v.4l8.5 6 8.5-6v-.4z" fill-rule="evenodd"/>
        </svg>
        belinda@theloombriefing.example
      </li>
      <li class="contact-item">
        <svg class="contact-icon" viewBox="0 0 24 24" aria-hidden="true">
          <path d="M12 2a10 10 0 1 0 0 20 10 10 0 0 0 0-20zm-1 17.9A8 8 0 0 1 4.1 10.1L9 15v1a2 2 0 0 0 2 2zm6.9-2.5A2 2 0 0 0 16 16h-1v-3a1 1 0 0 0-1-1H8v-2h2a1 1 0 0 0 1-1V7h2a2 2 0 0 0 2-2v-.4a8 8 0 0 1 2.9 12.8z"/>
        </svg>
        www.theloombriefing.example
      </li>
    </ul>

    <p class="tagline">Corporate Workwear &amp; Uniform Specialist | Personal Stylist</p>
  </main>
</body>
</html>
```